Brochure to attract insurance agents to outsource their bookkeeping

I need a brochure to handout at trade shows. Company name is Broker Office Ledger & Records. We go by BOLR. We provide bookkeeping services. I have attached the current brochure, which is a few years old, stale and outdated (not created on Pixmundo). I have also attached our graphic identity manual which show fonts/colors as well as our logo in 3 styles

Target Market(s)

Insurance Agents needing bookkeeping services

Industry/Entity Type

Accounting

Other font styles liked:
• See the graphic id manual

Colors
00AB8E
00BBA5
67D7C9
C6EFE9
E9F9F6

Requirements
Must have
• Services noted (see current brochure), contact info, reference to Vantrel Core

```html
<!DOCTYPE html>
<html lang="en">
<head>
<meta charset="utf-8">
<title>BOLR Brochure</title>
<link href="https://fonts.googleapis.com/css2?family=Poppins:wght@400;500;600&family=Nunito+Sans:wght@400;600;700&display=swap" rel="stylesheet">
<style>
:root{
  --green:#4be889;
  --green-light:#8cf1a6;
  --green-pale:#c8f8d6;
  --green-text:#3fe07f;
  --ink:#1c1c1c;
  --grey-tag:#8d9191;
  --backdrop:#b4bfbc;
  --paper:#ffffff;
}
*{margin:0;padding:0;box-sizing:border-box}
html,body{width:1200px;height:2498px;overflow:hidden}
body{background:var(--backdrop);position:relative;font-family:"Nunito Sans",sans-serif;color:var(--ink)}
.spread{position:absolute;left:78px;width:1070px;height:825px;background:var(--paper);overflow:hidden}
.spread-outer{top:58px}
.spread-inner{top:915px}
.abs{position:absolute}
.head{font-family:"Poppins",sans-serif;font-weight:500;line-height:1.45}
.accent{color:var(--green-text)}
.body-copy{font-size:11px;line-height:14.6px}
.photo{position:absolute;border-radius:50%;border:7px solid var(--green-light);background:radial-gradient(circle at 50% 40%,#d9c5b8,#6f7b86)}
.tag{position:absolute;font-size:10px;color:#fff;padding-left:8px}
.tag-name{background:var(--green);height:15px;line-height:15px}
.tag-role{background:var(--grey-tag);height:18px;line-height:18px}
.wordmark{font-family:"Poppins",sans-serif;font-weight:600;display:flex;align-items:center;gap:8px}
.wordmark i{display:inline-block;background:currentColor}
.phone{font-family:"Poppins",sans-serif;color:#fff;display:flex;align-items:center;gap:6px}
.services{position:absolute;left:826px;top:140px}
.service{position:absolute;left:0;width:240px;height:56px}
.service .icon{position:absolute;left:0;top:0;width:54px;height:54px;border-radius:14px;background:var(--green-pale);display:flex;align-items:center;justify-content:center}
.service .icon span{width:36px;height:36px;border-radius:9px;background:var(--green);display:flex;align-items:center;justify-content:center;color:#fff;font-family:"Poppins",sans-serif;font-weight:600;font-size:17px}
.service p{position:absolute;left:69px;top:8px;font-family:"Poppins",sans-serif;font-size:14px;line-height:19px}
.service-line{position:absolute;left:853px;top:190px;width:2px;height:470px;background:var(--green-light)}
.step{position:absolute;width:200px;font-size:11px;line-height:14.6px;padding-left:40px}
.step svg{position:absolute;left:0;top:0}
.card{position:absolute;border-radius:14px;background:linear-gradient(135deg,var(--green),var(--green-light));color:#fff}
.card h3{font-family:"Poppins",sans-serif;font-weight:500;font-size:11.5px;line-height:14.5px}
.card p{font-size:8.4px;line-height:11.3px;opacity:.85}
.badge{position:absolute;width:28px;height:28px;border-radius:50%;background:#fff;display:flex;align-items:center;justify-content:center}
.badge-solid{background:var(--green)}
.why h4{font-family:"Poppins",sans-serif;font-weight:500;font-size:11.5px;line-height:14.5px}
.why p{font-size:8.6px;line-height:11.2px}
.fees{position:absolute;left:820px;top:260px;width:226px;border-collapse:collapse;font-family:"Poppins",sans-serif;font-size:12px}
.fees th{font-weight:500;height:68px;line-height:16px;font-size:12px}
.fees th.rev{background:var(--green);color:#fff;width:116px}
.fees th.fee{background:#e9ecec}
.fees td{height:21.5px;padding:0 12px}
.fees td.amt{text-align:right}
.fees tr.shade td{background:#e6fbec}
</style>
</head>
<body>

<!-- OUTER SPREAD -->
<section class="spread spread-outer">
  <!-- About panel -->
  <h1 class="abs head" style="left:21px;top:38px;width:480px;font-size:19.5px;line-height:31px">
    <span class="accent">BOLR is a professional Accounting/Bookkeeping firm</span> located in Connecticut dedicated exclusively to Independent Insurance Agencies
  </h1>
  <div class="photo" role="img" aria-label="Portrait of the firm's principal" style="left:58px;top:161px;width:160px;height:160px"></div>
  <div class="photo" role="img" aria-label="Portrait of the Director of Accounting" style="left:280px;top:177px;width:100px;height:100px"></div>
  <div class="photo" role="img" aria-label="Portrait of an accountant" style="left:405px;top:262px;width:100px;height:100px"></div>
  <div class="photo" role="img" aria-label="Portrait of an accountant" style="left:284px;top:367px;width:100px;height:100px"></div>

  <div class="tag tag-name" style="left:387px;top:195px;width:94px">Evan Strade</div>
  <div class="tag tag-role" style="left:387px;top:211px;width:118px">Director of Accounting</div>
  <div class="tag tag-name" style="left:311px;top:298px;width:84px;text-align:right;padding-right:8px">Lena Marsh</div>
  <div class="tag tag-role" style="left:288px;top:314px;width:107px;text-align:right;padding-right:8px">Accountant</div>
  <div class="tag tag-name" style="left:395px;top:410px;width:92px">Colin Varda</div>
  <div class="tag tag-role" style="left:395px;top:427px;width:118px">Accountant</div>

  <div class="abs body-copy" style="left:21px;top:339px;width:236px">
    <p>BOLR's mission is to provide Independent Insurance Agencies a resource to have their accounting and bookkeeping performed accurately, timely and cost effectively. BOLR's 35 member staff is led by Maren Holloway.</p>
    <p style="margin-top:14px">Maren worked in Independent Insurance Agencies for several years before forming BOLR in 2011. Her experience includes accounting, operational management, and client service. She earned a bachelor's degree in accounting from Northfield State University and a master's degree in business administration from the University of Eastbrook. Maren is an adjunct accounting professor at Eastbrook Community Colleges. She serves her community as President of the local Civic Service Club</p>
  </div>
  <p class="abs" style="left:282px;top:520px;width:230px;text-align:center;font-size:9.5px;line-height:19px">For a complete list of BOLR staff and their profiles,<br><b style="font-size:10.5px">www.brokerledgerrecords.com</b></p>

  <svg class="abs" style="left:0;top:625px" width="536" height="200" viewBox="0 0 536 200">
    <path d="M0 12 C180 0 380 30 536 60 L536 200 L0 200Z" fill="var(--green-light)"/>
    <path d="M0 40 C180 30 380 55 536 80 L536 200 L0 200Z" fill="var(--green)"/>
  </svg>
  <p class="abs head" style="left:29px;top:714px;width:240px;color:#fff;font-size:19px;line-height:26px;font-weight:400">Let BOLR be an integral part of your Agency's success.</p>
  <div class="abs wordmark" style="left:292px;top:738px;color:#fff;font-size:30px"><i style="width:12px;height:12px"></i>BOLR</div>
  <p class="abs" style="left:421px;top:748px;color:#fff;font-size:9px;line-height:13px">47 Alder Mill Road<br>Westbrook, CT 06000</p>
  <p class="abs" style="left:421px;top:778px;color:#fff;font-family:Poppins,sans-serif;font-size:13px">555.018.2240</p>

  <!-- Cover panel -->
  <div class="abs wordmark" style="left:605px;top:50px;color:var(--green);font-size:46px;letter-spacing:1px"><i style="width:16px;height:16px"></i>BOLR</div>
  <div class="abs" role="img" aria-label="Photo of hands reviewing financial charts with a calculator" style="left:536px;top:130px;width:267px;height:300px;background:linear-gradient(160deg,#f2f4f4,#c9d0d2 60%,#8e9aa0)"></div>
  <svg class="abs" style="left:536px;top:125px" width="267" height="60" viewBox="0 0 267 60">
    <path d="M0 0 L267 0 L267 18 C200 5 120 -5 0 10Z" fill="#fff"/>
  </svg>
  <svg class="abs" style="left:536px;top:360px" width="267" height="465" viewBox="0 0 267 465">
    <path d="M0 40 C80 0 180 0 267 30 L267 465 L0 465Z" fill="var(--green)"/>
    <circle cx="130" cy="240" r="135" fill="var(--green-light)" opacity=".45"/>
  </svg>
  <h2 class="abs head" style="left:565px;top:470px;width:225px;color:#fff;font-size:29px;line-height:32px">Need help with Vantrel Core accounting?</h2>
  <p class="abs" style="left:569px;top:590px;width:205px;color:#fff;font-family:Poppins,sans-serif;font-size:16.5px;line-height:24px">The leading remote bookkeeping firm for Vantrel Core agencies nationwide</p>
  <div class="abs phone" style="left:578px;top:750px;font-size:18px">
    <svg width="20" height="20" viewBox="0 0 20 20"><circle cx="10" cy="10" r="10" fill="#fff"/><path d="M6.5 5 L8.5 5 L9.3 7.6 L8 8.6 C8.7 10.2 9.8 11.3 11.4 12 L12.4 10.7 L15 11.5 L15 13.5 C15 14.2 14.3 14.8 13.5 14.7 C9.2 14.2 5.8 10.8 5.3 6.5 C5.2 5.7 5.8 5 6.5 5Z" fill="var(--green)"/></svg>
    555.018.2240
  </div>

  <!-- Services panel -->
  <h2 class="abs head" style="left:827px;top:58px;font-size:24px"><span class="accent">Services</span> Available</h2>
  <div class="service-line"></div>
  <div class="services">
    <div class="service" style="top:0"><div class="icon"><span>$</span></div><p>Record Direct<br>Bill Commission</p></div>
    <div class="service" style="top:72px"><div class="icon"><span>&#8801;</span></div><p>Reconcile General<br>Ledger Accounts</p></div>
    <div class="service" style="top:151px"><div class="icon"><span>$</span></div><p>Pay Vendor<br>Invoices</p></div>
    <div class="service" style="top:231px"><div class="icon"><span>&#10003;</span></div><p>Reconcile &amp; Pay<br>Agency Bill Premiums</p></div>
    <div class="service" style="top:309px"><div class="icon"><span>&#9636;</span></div><p>Prepare &amp; Interpret<br>Financial Statements</p></div>
    <div class="service" style="top:392px"><div class="icon"><span>$</span></div><p>Reconcile Customer<br>Accounts Receivable</p></div>
    <div class="service" style="top:470px"><div class="icon"><span>$</span></div><p style="top:16px">Process Payroll</p></div>
  </div>
  <svg class="abs" style="left:803px;top:700px" width="267" height="125" viewBox="0 0 267 125">
    <path d="M0 20 C90 12 180 8 267 0 L267 125 L0 125Z" fill="var(--green-light)"/>
    <path d="M0 36 C90 28 180 22 267 16 L267 125 L0 125Z" fill="var(--green)"/>
  </svg>
  <div class="abs phone" style="left:895px;top:756px;font-size:18px">
    <svg width="20" height="20" viewBox="0 0 20 20"><circle cx="10" cy="10" r="10" fill="#fff"/><path d="M6.5 5 L8.5 5 L9.3 7.6 L8 8.6 C8.7 10.2 9.8 11.3 11.4 12 L12.4 10.7 L15 11.5 L15 13.5 C15 14.2 14.3 14.8 13.5 14.7 C9.2 14.2 5.8 10.8 5.3 6.5 C5.2 5.7 5.8 5 6.5 5Z" fill="var(--green)"/></svg>
    555.018.2240
  </div>
  <p class="abs" style="left:803px;top:782px;width:267px;text-align:center;color:#fff;font-size:10px">www.brokerledgerrecords.com</p>
</section>

<!-- INNER SPREAD -->
<section class="spread spread-inner">
  <!-- How it works -->
  <h2 class="abs head" style="left:20px;top:38px;font-size:26.5px"><span class="accent">How outsourcing</span> to BOLR works</h2>
  <p class="abs body-copy" style="left:20px;top:92px;width:410px;font-size:11px">We access your Vantrel Core online database in the same manner as Agency staff. You provide the login credentials. Below is a high-level overview of the process. A detailed operational workflow is provided to each client Agency.</p>

  <div class="step" style="left:22px;top:188px"><svg width="22" height="22" viewBox="0 0 22 22"><circle cx="11" cy="11" r="11" fill="var(--green)"/><path d="M6 11.5 L9.5 15 L16 8" stroke="#fff" stroke-width="2.2" fill="none"/></svg>Agency staff routes accounting documents to BOLR through Vantrel Core.</div>
  <div class="step" style="left:22px;top:241px"><svg width="22" height="22" viewBox="0 0 22 22"><circle cx="11" cy="11" r="11" fill="var(--green)"/><path d="M6 11.5 L9.5 15 L16 8" stroke="#fff" stroke-width="2.2" fill="none"/></svg>Agency staff makes bank deposits of paper checks and cash, routing documentation to BOLR to record in Vantrel Core. BOLR records EFT transactions from the bank records.</div>
  <div class="step" style="left:22px;top:348px"><svg width="22" height="22" viewBox="0 0 22 22"><circle cx="11" cy="11" r="11" fill="var(--green)"/><path d="M6 11.5 L9.5 15 L16 8" stroke="#fff" stroke-width="2.2" fill="none"/></svg>BOLR pays your vendors and insurance companies/brokers via Vantrel Core checks that you print, or via your bank's bill pay system, or via ACH. Agencies may choose the method.</div>
  <div class="step" style="left:22px;top:455px"><svg width="22" height="22" viewBox="0 0 22 22"><circle cx="11" cy="11" r="11" fill="var(--green)"/><path d="M6 11.5 L9.5 15 L16 8" stroke="#fff" stroke-width="2.2" fill="none"/></svg>BOLR reconciles Agency staff invoicing of all agency bill transactions with insurance company/broker records at time of payment. We work with your staff on discrepancies.</div>
  <div class="step" style="left:280px;top:186px;width:240px"><svg width="22" height="22" viewBox="0 0 22 22"><circle cx="11" cy="11" r="11" fill="var(--green)"/><path d="M6 11.5 L9.5 15 L16 8" stroke="#fff" stroke-width="2.2" fill="none"/></svg>BOLR records all direct bill commission at the time commission is received; this includes downloads, imports, and manual entry. You provide the commission statements or provide online access for BOLR to obtain.</div>
  <div class="step" style="left:280px;top:307px;width:240px"><svg width="22" height="22" viewBox="0 0 22 22"><circle cx="11" cy="11" r="11" fill="var(--green)"/><path d="M6 11.5 L9.5 15 L16 8" stroke="#fff" stroke-width="2.2" fill="none"/></svg>BOLR reconciles all bank accounts in Vantrel Core with your bank's data at least twice per week. You provide the login credentials.</div>
  <div class="step" style="left:280px;top:387px;width:240px"><svg width="22" height="22" viewBox="0 0 22 22"><circle cx="11" cy="11" r="11" fill="var(--green)"/><path d="M6 11.5 L9.5 15 L16 8" stroke="#fff" stroke-width="2.2" fill="none"/></svg>BOLR sends financial statements to Agency Principals each month. We encourage review and discussion.</div>

  <div class="abs" role="img" aria-label="Photo of a hand with a pen over a calculator and charts, tinted green" style="left:0;top:565px;width:536px;height:260px;background:linear-gradient(135deg,#7fe7a3,#5fd58c 45%,#3f9e74)"></div>
  <svg class="abs" style="left:0;top:555px" width="536" height="60" viewBox="0 0 536 60">
    <path d="M0 0 L536 0 L536 48 C380 12 180 4 0 18Z" fill="#fff"/>
  </svg>

  <!-- Why it works -->
  <h2 class="abs head" style="left:557px;top:33px;font-size:19.5px;line-height:27px"><span class="accent">Why outsourcing</span> to<br>BOLR works</h2>
  <div class="card" style="left:551px;top:114px;width:238px;height:228px;padding:17px 12px 0 52px">
    <div class="badge" style="left:19px;top:18px"><svg width="16" height="16" viewBox="0 0 16 16"><circle cx="8" cy="5" r="3" fill="var(--green)"/><path d="M2 15 C2 10 14 10 14 15Z" fill="var(--green)"/></svg></div>
    <h3>Our Staff is Educated in Accounting &amp; Trained<br>in Vantrel Core</h3>
    <p style="margin:8px 0 0 -33px">The BOLR staff consists of Accountants, Bookkeepers, and Clerks. All are well trained in their responsibilities for Vantrel Core accounting. Accountants have earned bachelor's degrees in accounting and have several years of Vantrel Core experience. Bookkeepers have earned associate degree credits in accounting or have significant bookkeeping experience. Clerks have a variety of experiences and education levels, many are in school for accounting, all are detail oriented numbers people. Agency clients get the benefit of a full BOLR team.</p>
  </div>
  <div class="why abs" style="left:557px;top:355px;width:235px">
    <div class="badge badge-solid" style="left:0;top:0"><svg width="14" height="14" viewBox="0 0 14 14"><path d="M2 7.5 L5.5 11 L12 3" stroke="#fff" stroke-width="2" fill="none"/></svg></div>
    <h4 style="margin-left:43px">Our Work goes through a Quality Control Process</h4>
    <p style="margin-top:14px">BOLR has a proprietary system of checks and balances to ensure client's financial statements are complete and accurate. All financial statement packages are prepared by our bookkeeping staff and reviewed by a staff accountant before presentation to the client. Agency principals are encouraged to discuss their statements with their BOLR accountant. Our goal is for our clients to understand their financial data, empowering them to make sound financial decisions.</p>
  </div>
  <div class="card" style="left:556px;top:515px;width:230px;height:115px;padding:27px 12px 0 56px">
    <div class="badge" style="left:19px;top:20px"><svg width="14" height="14" viewBox="0 0 14 14"><path d="M11 7 A4 4 0 1 1 7 3 L9 3" stroke="var(--green)" stroke-width="1.8" fill="none"/><path d="M8 1 L10 3 L8 5" stroke="var(--green)" stroke-width="1.6" fill="none"/></svg></div>
    <h3>We always have a Backup</h3>
    <p style="margin:12px 0 0 -34px">When your BOLR Bookkeeper is out of the office a backup is always available. Should your BOLR Bookkeeper leave BOLR, another trained staff member will be available.</p>
  </div>
  <div class="why abs" style="left:551px;top:655px;width:240px">
    <div class="badge badge-solid" style="left:0;top:0;width:32px;height:32px"><svg width="14" height="14" viewBox="0 0 14 14"><rect x="2" y="1" width="10" height="12" rx="1" fill="#fff"/><path d="M4 5 H10 M4 8 H10" stroke="var(--green)" stroke-width="1.2"/></svg></div>
    <h4 style="margin-left:43px;margin-top:4px">We Implement Controls for Data Security</h4>
    <p style="margin-top:20px">All computer equipment is owned by BOLR. PCs and routers are regularly updated to stay current with technology. All are continuously monitored for system updates and virus/malware by an independent IT firm. Dual authentication is required for remote access to our PCs. Documents are shared within Vantrel Core or through a secure document sharing platform, Fileway Vault.</p>
  </div>

  <!-- Fees -->
  <h2 class="abs head" style="left:826px;top:30px;font-size:19.5px;line-height:28px"><span class="accent">How the BOLR FEES</span><br>are structured</h2>
  <p class="abs body-copy" style="left:826px;top:102px;width:222px;font-size:10.5px">Fees are a flat monthly rate based on annual policy commission revenue. The table below lists sample rates for our full-service offerings at different revenue volumes for an Agency with a typical mix of business and complexity. Fees assume compliance with our standard operating workflows.</p>
  <table class="fees">
    <tr><th class="rev">Annual<br>Commission<br>Revenue</th><th class="fee">Monthly<br>Service<br>Fee</th></tr>
    <tr><td>&lt;$300,000</td><td class="amt">$600</td></tr>
    <tr class="shade"><td>$700,000</td><td class="amt">$1,400</td></tr>
    <tr><td>$1,000,000</td><td class="amt">$2,000</td></tr>
    <tr class="shade"><td>$1,500,000</td><td class="amt">$2,500</td></tr>
    <tr><td>$2,000,000</td><td class="amt">$3,000</td></tr>
    <tr class="shade"><td>$2,500,000</td><td class="amt">$3,500</td></tr>
    <tr><td>$3,000,000</td><td class="amt">$4,500</td></tr>
  </table>
  <p class="abs body-copy" style="left:824px;top:509px;width:222px;font-size:10.5px">We can provide services for larger agencies, typically supplementing in-house staff.</p>
  <div class="abs" role="img" aria-label="Photo of a calculator, pie charts and banknotes on paperwork" style="left:803px;top:580px;width:267px;height:130px;background:linear-gradient(120deg,#e9eef0,#b9cbd4 50%,#8fb0a0)"></div>
  <svg class="abs" style="left:803px;top:575px" width="267" height="250" viewBox="0 0 267 250">
    <path d="M0 0 L267 0 L267 5 C180 -2 80 2 0 12Z" fill="#fff"/>
    <path d="M0 130 C90 112 180 98 267 80 L267 250 L0 250Z" fill="var(--green-light)"/>
    <path d="M0 145 C90 128 180 114 267 98 L267 250 L0 250Z" fill="var(--green)"/>
  </svg>
  <div class="abs phone" style="left:848px;top:743px;font-size:21px">
    <svg width="28" height="28" viewBox="0 0 20 20"><circle cx="10" cy="10" r="10" fill="#fff"/><path d="M6.5 5 L8.5 5 L9.3 7.6 L8 8.6 C8.7 10.2 9.8 11.3 11.4 12 L12.4 10.7 L15 11.5 L15 13.5 C15 14.2 14.3 14.8 13.5 14.7 C9.2 14.2 5.8 10.8 5.3 6.5 C5.2 5.7 5.8 5 6.5 5Z" fill="var(--green)"/></svg>
    555.018.2240
  </div>
  <p class="abs" style="left:803px;top:780px;width:267px;text-align:center;color:#fff;font-size:8px">www.brokerledgerrecords.com</p>
  <p class="abs" style="left:803px;top:797px;width:267px;text-align:center;color:#fff;font-size:5.5px">Vantrel Core is a registered trademark of Vantrel Systems, Inc.</p>
</section>

</body>
</html>
```